Business Card: RW Office Partners - Your organised problem solver

Business Name: RW Office Partners
Website: www.rwofficepartners.com.au
Email: marisol@rwofficepartners.com.au
Mobile: 61 482 907 236
Facebook: @rwofficepartners
Instrgram: @rwofficepartners

Brading Colours:
HEX
#986474
#ddccd3
#7a8498
#c9d8e4
#000000
#ffffff

Tag Line: Your organised problem solver

Link to DRAFT website:
https://deskhelpcollective.wixsite.com/rw-office-partners

About Page from the website:
My name is Marisol Wrenfield, and I would love to assist you to become more productive in your day to day and achieve your business and personal goals.
My mission is to give you time, time to work on the important tasks of your business or to be able to spend more time with your family. I will take on the tasks you don’t have time for, don’t know well or simply don’t like to do.
I have an extensive background in Administration, Tender Coordination, Document Control, WHS and Quality Management working primarily in the Construction, Mining and Corporate World.
I am passionate about being organised, having order and making things in your life (and mine) easier! I love to watch something unfold and grow into something amazing! I am known for being the go-to problem solver, the organiser of all things, producing high standards of work even under pressure. I’m also a confident communicator, and I understand that you’re busy running your business.

Target Market(s)

Small to Medium Business who require assistance in their business by a virtual assistant.

Industry/Entity Type

Virtual Assistant

Contact Information for Business Card

Mobile: 61 482 907 236

Font styles to use
Sans Serif

Colors
ffffff

Requirements
Must have
• Branding Colours as outlined.
Contact Details as outlined.
Logo as provided.
Proper contact details - mobile, facebook, instragm, website.
Simple, Elegant, very clean looking.
Should not have
• Note cute with pictures.
Not too girly as still want to market to construction companies.

```html
<!DOCTYPE html>
<html lang="en">
<head>
<meta charset="utf-8">
<title>RW Office Partners – Business Card</title>
<link rel="stylesheet" href="https://fonts.googleapis.com/css2?family=Montserrat:wght@500;600&family=Roboto:wght@400;500&display=swap">
<style>
  :root {
    --backdrop: #3a3a3c;
    --card: #1c1b1f;
    --mauve: #986474;
    --mauve-light: #ddccd3;
    --slate: #7a8498;
    --slate-light: #c9d8e4;
    --emboss: #86858b;
    --white: #ffffff;
    --divider: #8d8a92;
  }
  * { box-sizing: border-box; margin: 0; padding: 0; }
  html, body { width: 799px; height: 1200px; overflow: hidden; }
  body {
    background: var(--backdrop);
    font-family: "Roboto", Arial, sans-serif;
    color: var(--white);
    position: relative;
  }
  .card {
    position: absolute;
    left: 100px;
    width: 600px;
    height: 343px;
    background: var(--card);
    border-radius: 3px;
    box-shadow: 0 14px 30px rgba(0,0,0,.45);
    overflow: hidden;
  }
  .card--front { top: 120px; }
  .card--back { top: 700px; }

  .brand {
    position: absolute;
    font-family: "Montserrat", Arial, sans-serif;
    font-weight: 600;
    letter-spacing: .5px;
    white-space: nowrap;
  }
  .card--front .brand {
    right: 56px; top: 118px;
    font-size: 42px; line-height: 1.05;
    color: var(--emboss);
    text-align: right;
  }
  .card--back .brand {
    right: 56px; top: 58px;
    font-size: 36px; line-height: 1.05;
    color: var(--slate);
    text-align: right;
  }

  .socials {
    position: absolute;
    display: flex; gap: 26px;
    font-size: 15px;
    color: var(--white);
  }
  .card--front .socials { left: 60px; bottom: 58px; }
  .card--back .socials { left: 60px; bottom: 26px; }
  .socials__item { display: flex; align-items: center; gap: 8px; }
  .socials__mark {
    width: 11px; height: 11px;
    background: var(--mauve);
    border-radius: 2px;
  }

  .person {
    position: absolute;
    right: 380px; top: 150px;
    text-align: right;
  }
  .person__name {
    font-family: "Montserrat", Arial, sans-serif;
    font-weight: 600;
    font-size: 19px;
    color: var(--mauve);
  }
  .person__title { font-size: 14px; margin-top: 20px; color: var(--white); }
  .name-rule {
    position: absolute;
    left: 0; top: 180px;
    width: 212px; height: 13px;
    background: var(--mauve);
  }
  .divider {
    position: absolute;
    left: 234px; top: 158px;
    width: 1px; height: 72px;
    background: var(--divider);
  }
  .contact {
    position: absolute;
    left: 252px; top: 164px;
    list-style: none;
    font-size: 14.5px;
    line-height: 23px;
  }
  .contact li { display: flex; align-items: center; gap: 10px; }
  .contact svg { width: 12px; height: 12px; fill: var(--mauve); flex: none; }

  .tagline-band {
    position: absolute;
    left: 0; top: 246px;
    width: 100%; height: 28px;
    background: linear-gradient(90deg, var(--mauve) 0%, #8d7187 45%, var(--slate) 100%);
    display: flex; align-items: center;
    padding-left: 40px;
  }
  .tagline {
    font-family: "Montserrat", Arial, sans-serif;
    font-weight: 500;
    font-size: 13.5px;
    letter-spacing: 2.4px;
    text-transform: uppercase;
    word-spacing: 5px;
    color: var(--white);
  }
</style>
</head>
<body>

<section class="card card--front" aria-label="Card front">
  <div class="brand">RW Office Partners</div>
  <ul class="socials">
    <li class="socials__item"><span class="socials__mark"></span>@rwofficepartners</li>
    <li class="socials__item"><span class="socials__mark"></span>@rwofficepartners</li>
  </ul>
</section>

<section class="card card--back" aria-label="Card back">
  <div class="brand">RW Office Partners</div>

  <div class="person">
    <div class="person__name">Marisol Wrenfield</div>
    <div class="person__title">Virtual Assistant</div>
  </div>
  <div class="name-rule"></div>
  <div class="divider"></div>

  <ul class="contact">
    <li>
      <svg viewBox="0 0 12 12" aria-hidden="true"><path d="M2.4 0.5 4.3 2.6 3.3 4c.7 1.6 2 2.9 3.7 3.7l1.4-1 2.1 1.9-1.2 2.1C5 10.5 1.5 7 .3 1.7z"/></svg>
      61 482 907 236
    </li>
    <li>
      <svg viewBox="0 0 12 12" aria-hidden="true"><path d="M0 2h12v1.2L6 7 0 3.2z M0 4.6l6 3.8 6-3.8V10H0z"/></svg>
      marisol@rwofficepartners.com.au
    </li>
    <li>
      <svg viewBox="0 0 12 12" aria-hidden="true"><path d="M6 0a6 6 0 1 0 0 12A6 6 0 0 0 6 0zm0 1.2c.8.9 1.3 2.5 1.4 4.2H4.6C4.7 3.7 5.2 2.1 6 1.2zM1.2 6.6h2.2c.1 1.6.5 3 1.1 4A4.8 4.8 0 0 1 1.2 6.6zm0-1.2a4.8 4.8 0 0 1 3.3-4c-.6 1-1 2.4-1.1 4zm3.4 1.2h2.8c-.1 1.7-.6 3.3-1.4 4.2-.8-.9-1.3-2.5-1.4-4.2zm2.9 4c.6-1 1-2.4 1.1-4h2.2a4.8 4.8 0 0 1-3.3 4zm1.1-5.2c-.1-1.6-.5-3-1.1-4a4.8 4.8 0 0 1 3.3 4z"/></svg>
      www.rwofficepartners.com.au
    </li>
  </ul>

  <div class="tagline-band"><span class="tagline">Your organised problem solver</span></div>

  <ul class="socials">
    <li class="socials__item"><span class="socials__mark"></span>@rwofficepartners</li>
    <li class="socials__item"><span class="socials__mark"></span>@rwofficepartners</li>
  </ul>
</section>

</body>
</html>
```